PlumVesta screens tidy up

We would like advice on how to better present the following home page and overview pages.

The existing website is functional, but the pages don't appear professionals and pleasing to the eye. We would specifically like feedback on alignment and padding of icons and text to make the screen more appealing and polished.

We are following the quartzline design system.

1 page

Sans Serif
• IBM Plex, Poppins

```html
<!DOCTYPE html>
<html lang="en">
<head>
<meta charset="utf-8">
<title>PlumVesta screens</title>
<link href="https://fonts.googleapis.com/css2?family=Poppins:wght@400;500;600;700;800&display=swap" rel="stylesheet">
<style>
:root{
  --page:#dcdcdc;
  --sidebar:#3e3d3c;
  --panel-dark:#42403e;
  --header:#f6aa44;
  --orange:#ee8224;
  --card:#f6aa44;
  --accent:#f08a27;
  --blue:#1463ff;
  --white:#ffffff;
  --line:#f2b074;
}
*{box-sizing:border-box;margin:0;padding:0}
html,body{width:1200px;height:2261px;overflow:hidden}
body{background:var(--page);font-family:"Poppins",sans-serif;color:var(--white);position:relative}
.screen{position:absolute;left:85px;width:1030px;background:var(--white);overflow:hidden}
.screen--home{top:101px;height:946px}
.screen--overview{top:1140px;height:1020px}
.sidebar{position:absolute;left:0;top:0;width:250px;height:100%;background:var(--sidebar)}
.brand{position:absolute;left:14px;top:14px;display:flex;align-items:center;gap:12px;height:56px}
.brand-dot{width:44px;height:44px;border-radius:50%;background:var(--accent)}
.brand-name{font-size:28px;font-weight:500;letter-spacing:-0.5px;color:var(--white)}
.nav-item{position:absolute;left:10px;width:230px;height:40px;display:flex;align-items:center;padding-left:60px;font-size:13px;color:var(--white)}
.nav-item svg{position:absolute;left:34px;top:12px;width:16px;height:16px}
.nav-item--active{background:var(--white);color:var(--accent)}
.nav-item--heading{font-size:17px;font-weight:700}
.nav-item .plus{position:absolute;right:2px;font-size:16px;font-weight:700}
.nav-item .chev{position:absolute;right:6px;top:14px;width:11px;height:11px}
.nav-item--sub{padding-left:60px}
.nav-item--current{left:44px;width:206px;height:30px;padding-left:26px;border:1.5px solid var(--white);color:var(--accent)}
.topbar{position:absolute;left:250px;top:0;right:0;height:84px;background:var(--header)}
.topbar h1{position:absolute;left:32px;top:22px;font-size:26px;font-weight:700}
.topbar .crumb{position:absolute;left:33px;top:17px;font-size:13px;font-weight:400}
.topbar .title{position:absolute;left:33px;top:34px;font-size:26px;font-weight:700}
.topbar .avatar{position:absolute;right:24px;top:22px;width:34px;height:34px}
.box{position:absolute}
.box--dark{background:var(--panel-dark)}
.box--orange{background:var(--orange)}
.box-head{height:53px;display:flex;align-items:center;justify-content:center;font-size:23px;font-weight:700;border-bottom:1px solid #6b6966;margin:0 2px}
.box--orange .box-head{border-bottom-color:var(--line)}
.box-head--left{justify-content:flex-start;padding-left:42px;color:var(--accent)}
.teamspace-body{text-align:center;padding-top:12px}
.teamspace-body strong{display:block;font-size:17px;font-weight:700}
.teamspace-body span{font-size:13px}
.stat-label{position:absolute;font-size:17px;font-weight:700;display:flex;align-items:center;gap:12px}
.stat-label svg{width:42px;height:36px}
.counter{position:absolute;display:flex;align-items:center;gap:10px;font-size:17px;font-weight:700}
.counter svg{width:26px;height:26px}
.progress{position:absolute;left:45px;width:280px;height:2px;background:#f6c9a0}
.progress i{display:block;width:12px;height:3px;background:var(--panel-dark);margin-top:-0.5px}
.btn{position:absolute;background:var(--blue);color:var(--white);font-size:11px;display:flex;align-items:center;padding:0 14px}
.campaign-card{position:absolute;top:80px;width:304px;height:282px;background:var(--card);text-align:center;padding-top:10px}
.campaign-card h3{font-size:23px;font-weight:700}
.campaign-card .desc{font-size:11.5px;margin-top:2px}
.campaign-card .badge{width:73px;height:73px;border-radius:50%;background:var(--panel-dark);margin:16px auto 0;display:flex;align-items:center;justify-content:center}
.campaign-card .badge svg{width:42px;height:42px}
.campaign-card .num{font-size:26px;color:var(--blue);line-height:1;margin-top:14px}
.campaign-card .state{font-size:13px;margin-top:2px}
.campaign-card .kind{font-size:13px;font-weight:700;margin-top:2px}
.campaign-card .since{font-size:9.5px;margin-top:14px}
.campaign-info{padding:12px 0 0 43px}
.campaign-info strong{font-size:19px;font-weight:700;display:block}
.campaign-info span{font-size:14px;padding-left:2px}
.org-col{position:absolute;top:96px;width:260px}
.org-col h4{font-size:18px;font-weight:700;line-height:29px}
.org-col p{font-size:14px;margin-top:9px}
.org-count{display:flex;align-items:center;gap:12px;margin-top:18px;font-size:32px;font-weight:700}
.org-count svg{width:52px;height:44px}
.resource-text{position:absolute;left:43px;top:126px;font-size:13.5px;line-height:22px;width:250px}
.alert-text{position:absolute;left:43px;top:124px;font-size:13.5px}
</style>
</head>
<body>

<svg width="0" height="0" style="position:absolute">
  <defs>
    <symbol id="i-home" viewBox="0 0 16 16"><path d="M8 1 1 7.5h2V15h4v-4h2v4h4V7.5h2z" fill="currentColor"/></symbol>
    <symbol id="i-bell" viewBox="0 0 16 16"><path d="M8 1a4.5 4.5 0 0 0-4.5 4.5V10L2 12h12l-1.5-2V5.5A4.5 4.5 0 0 0 8 1zm-2 12a2 2 0 0 0 4 0z" fill="currentColor"/></symbol>
    <symbol id="i-team" viewBox="0 0 16 16"><g fill="currentColor"><circle cx="5" cy="4" r="2"/><circle cx="11" cy="4" r="2"/><path d="M1 10a4 3 0 0 1 8 0zM7 10a4 3 0 0 1 8 0z"/><circle cx="8" cy="10" r="2"/><path d="M4 16a4 3 0 0 1 8 0z"/></g></symbol>
    <symbol id="i-mega" viewBox="0 0 24 24"><g fill="currentColor"><path d="M3 13l9-7 3 10-10 1z"/><path d="M6 16l2 5 2-1-1-4z"/><path d="M17 5l2-2M19 9l3-1M18 2l1-2" stroke="currentColor" stroke-width="1.6"/></g></symbol>
    <symbol id="i-chev-up" viewBox="0 0 12 12"><path d="M1 8l5-5 5 5" fill="none" stroke="currentColor" stroke-width="1.3"/></symbol>
    <symbol id="i-chev-down" viewBox="0 0 12 12"><path d="M1 4l5 5 5-5" fill="none" stroke="currentColor" stroke-width="1.3"/></symbol>
    <symbol id="i-user" viewBox="0 0 34 34"><g fill="none" stroke="#fff" stroke-width="2"><circle cx="17" cy="17" r="15"/><circle cx="17" cy="13" r="5"/><path d="M7 27c3-6 17-6 20 0"/></g></symbol>
    <symbol id="i-folder" viewBox="0 0 42 36"><g fill="none" stroke="#fff" stroke-width="1.5"><path d="M2 10h12l3 3h20v21H2z"/><path d="M14 13l10-10 10 10"/><path d="M37 13l3 3-4 18"/></g></symbol>
    <symbol id="i-check" viewBox="0 0 26 26"><g fill="none" stroke="#fff" stroke-width="1.6"><circle cx="13" cy="13" r="11.5"/><path d="M8 13l3.5 3.5L18 10"/></g></symbol>
    <symbol id="i-box" viewBox="0 0 26 26"><g fill="none" stroke="#fff" stroke-width="1.5"><path d="M2 11h22v13H2z"/><path d="M5 11l8-8 8 8"/><path d="M9 11l4-4 4 4"/></g></symbol>
    <symbol id="i-profile" viewBox="0 0 42 42"><g fill="none" stroke="#fff" stroke-width="1.6"><rect x="2" y="4" width="38" height="28"/><circle cx="13" cy="14" r="4"/><path d="M6 26c2-6 12-6 14 0"/><path d="M23 16l4 4 8-8"/><path d="M18 32l4 6 4-6"/></g></symbol>
    <symbol id="i-network" viewBox="0 0 52 44"><g fill="none" stroke="var(--accent)" stroke-width="1.8"><circle cx="16" cy="12" r="9"/><circle cx="38" cy="22" r="7"/><circle cx="24" cy="34" r="8"/><circle cx="5" cy="30" r="3"/><circle cx="48" cy="8" r="3"/><path d="M22 18l10 2M20 20l2 6M31 27l-3 3M8 28l7-3M46 10l-4 6"/></g></symbol>
    <symbol id="i-gear-people" viewBox="0 0 52 44"><g fill="none" stroke="#fff" stroke-width="1.5"><circle cx="26" cy="24" r="6"/><circle cx="26" cy="24" r="10" stroke-dasharray="4 3"/><circle cx="26" cy="5" r="3"/><circle cx="8" cy="28" r="3"/><circle cx="44" cy="28" r="3"/><path d="M3 40c1-6 9-6 10 0M39 40c1-6 9-6 10 0"/></g></symbol>
    <symbol id="i-warning" viewBox="0 0 46 40"><g fill="none" stroke="var(--accent)" stroke-width="2"><path d="M23 2 44 38H2z"/><path d="M23 14v12M23 30v3"/></g></symbol>
  </defs>
</svg>

<!-- Home screen -->
<section class="screen screen--home">
  <nav class="sidebar">
    <div class="brand"><span class="brand-dot"></span><span class="brand-name">PlumVesta</span></div>
    <div class="nav-item nav-item--active" style="top:85px"><svg><use href="#i-home"/></svg>Home</div>
    <div class="nav-item" style="top:128px"><svg><use href="#i-bell"/></svg>All alerts</div>
    <div class="nav-item" style="top:172px"><svg><use href="#i-team"/></svg>Manage</div>
    <div class="nav-item nav-item--heading" style="top:222px">Campaigns<span class="plus">+</span></div>
    <div class="nav-item nav-item--active" style="top:276px"><svg style="color:var(--accent)"><use href="#i-mega"/></svg>My Custom Campaign<svg class="chev"><use href="#i-chev-up"/></svg></div>
    <div class="nav-item nav-item--sub" style="top:319px">Overview</div>
    <div class="nav-item nav-item--sub" style="top:363px">Files&amp; Honey Tokens</div>
    <div class="nav-item nav-item--sub" style="top:407px">Resources</div>
    <div class="nav-item nav-item--sub" style="top:451px">Alerts</div>
    <div class="nav-item nav-item--sub" style="top:495px">Settings</div>
    <div class="nav-item nav-item--active" style="top:554px"><svg style="color:var(--accent)"><use href="#i-mega"/></svg>Default Campaign<svg class="chev"><use href="#i-chev-down"/></svg></div>
  </nav>
  <header class="topbar">
    <h1>Home</h1>
    <svg class="avatar"><use href="#i-user"/></svg>
  </header>

  <div class="box box--dark" style="left:270px;top:112px;width:739px;height:122px">
    <div class="box-head">Teamspace</div>
    <div class="teamspace-body"><strong>Default</strong><span>The Default Client is Creatrd as a Part of Your User Account.</span></div>
  </div>

  <div class="box box--orange" style="left:270px;top:269px;width:350px;height:210px">
    <div class="box-head">Subscription Overview</div>
    <svg style="position:absolute;left:44px;top:66px;width:42px;height:42px"><use href="#i-profile"/></svg>
    <div style="position:absolute;left:44px;top:125px;font-size:17px;font-weight:700">Starter Pack Usage</div>
    <div class="progress" style="top:160px"><i></i></div>
    <div style="position:absolute;left:43px;top:178px;font-size:13px">0 files Active out of 10 allowed</div>
  </div>

  <div class="box box--orange" style="left:654px;top:269px;width:350px;height:210px">
    <div class="box-head">Files&amp;HoneyTokens</div>
    <div class="stat-label" style="left:44px;top:61px"><svg><use href="#i-folder"/></svg>Statistics</div>
    <div class="counter" style="left:77px;top:154px"><svg><use href="#i-check"/></svg>0</div>
    <div class="counter" style="left:215px;top:154px"><svg><use href="#i-box"/></svg>30</div>
  </div>

  <div class="box box--dark" style="left:270px;top:514px;width:739px;height:385px">
    <div class="box-head">Campaigns</div>
    <div class="btn" style="left:579px;top:10px;width:151px;height:32px">New campaign<span style="margin-left:auto;font-size:14px">+</span></div>
    <article class="campaign-card" style="left:46px">
      <h3>My Custom Campaign</h3>
      <p class="desc">This is my Custom Campaign for finding i</p>
      <div class="badge"><svg style="color:#fff"><use href="#i-mega"/></svg></div>
      <div class="num">0</div><div class="state">Active</div>
      <div class="kind">Files and HoneyTokens</div>
      <div class="since">Active Since: Jul 25 2023 13:12</div>
    </article>
    <article class="campaign-card" style="left:390px">
      <h3>Default Campaign</h3>
      <p class="desc">Define your own mission,or Combine differen...</p>
      <div class="badge"><svg style="color:#fff"><use href="#i-mega"/></svg></div>
      <div class="num">0</div><div class="state">Active</div>
      <div class="kind">Files and HoneyTokens</div>
      <div class="since">Active Since: Jul 20 2023 12:17</div>
    </article>
  </div>
</section>

<!-- Overview screen -->
<section class="screen screen--overview">
  <nav class="sidebar">
    <div class="brand"><span class="brand-dot"></span><span class="brand-name">PlumVesta</span></div>
    <div class="nav-item nav-item--active" style="top:85px"><svg><use href="#i-home"/></svg>Home</div>
    <div class="nav-item" style="top:128px"><svg><use href="#i-bell"/></svg>All alerts</div>
    <div class="nav-item" style="top:172px"><svg><use href="#i-team"/></svg>Manage</div>
    <div class="nav-item nav-item--heading" style="top:222px">Campaigns<span class="plus">+</span></div>
    <div class="nav-item nav-item--active" style="top:276px"><svg style="color:var(--accent)"><use href="#i-mega"/></svg>My Custom Campaign<svg class="chev"><use href="#i-chev-up"/></svg></div>
    <div class="nav-item nav-item--current" style="top:324px">Overview</div>
    <div class="nav-item nav-item--sub" style="top:363px">Files&amp; Honey Tokens</div>
    <div class="nav-item nav-item--sub" style="top:407px">Resources</div>
    <div class="nav-item nav-item--sub" style="top:451px">Alerts</div>
    <div class="nav-item nav-item--sub" style="top:495px">Settings</div>
    <div class="nav-item nav-item--active" style="top:554px"><svg style="color:var(--accent)"><use href="#i-mega"/></svg>Default Campaign<svg class="chev"><use href="#i-chev-down"/></svg></div>
  </nav>
  <header class="topbar">
    <div class="crumb">My Custom Campaign</div>
    <div class="title">Overview</div>
    <svg class="avatar"><use href="#i-user"/></svg>
  </header>

  <div class="box box--dark" style="left:270px;top:111px;width:739px;height:122px">
    <div class="box-head box-head--left" style="border-bottom-color:var(--accent)">Campaign</div>
    <div class="btn" style="left:610px;top:10px;width:109px;height:28px;justify-content:center;font-size:14px">Custom</div>
    <div class="campaign-info"><strong>My Custom Campaign</strong><span>This is my custom campaign for finding i</span></div>
  </div>

  <div class="box box--dark" style="left:270px;top:258px;width:739px;height:279px">
    <div class="box-head box-head--left" style="height:58px;border-bottom-color:var(--accent)">Campaign Organisation</div>
    <div class="org-col" style="left:43px">
      <h4>Self-enabling Deliverbles<br>Proprietary Limited</h4>
      <p>This is my custom campaign for finding i</p>
      <div class="org-count"><svg><use href="#i-network"/></svg>86</div>
    </div>
    <div class="org-col" style="left:482px">
      <h4>Unleash bleeding-edge<br>mindshare</h4>
      <p>8 hours ago</p>
      <div class="org-count"><svg><use href="#i-network"/></svg>8</div>
    </div>
  </div>

  <div class="box box--orange" style="left:270px;top:572px;width:350px;height:210px">
    <div class="box-head">Files&amp;HoneyTokens</div>
    <div class="stat-label" style="left:44px;top:61px"><svg><use href="#i-folder"/></svg>Statistics</div>
    <div class="counter" style="left:77px;top:154px"><svg><use href="#i-check"/></svg>0</div>
    <div class="counter" style="left:215px;top:154px"><svg><use href="#i-box"/></svg>30</div>
  </div>

  <div class="box box--orange" style="left:659px;top:572px;width:350px;height:210px">
    <div class="box-head">Resources</div>
    <svg style="position:absolute;left:40px;top:66px;width:46px;height:40px"><use href="#i-gear-people"/></svg>
    <p class="resource-text">Generate a collection of fictional organisations, Custom templates, Uploaded files ans logos.</p>
  </div>

  <div class="box box--dark" style="left:270px;top:813px;width:739px;height:161px">
    <div class="box-head box-head--left">Resources</div>
    <svg style="position:absolute;left:45px;top:66px;width:38px;height:34px"><use href="#i-warning"/></svg>
    <p class="alert-text">Alert Statistics will appear here</p>
  </div>
</section>

</body>
</html>
```